Rise Past The Ridge - This will be the titles of the podcast. The podcast is all about self developen

I need a graphic design for a podcast please. This podcast is all about heeling people make a change in their life Topics of business, health and fitness, learning, relationships. Pretty much anything to do with living a legendary life. I have not yet got a logo designed yet but will look at doing this in conjunction with this project.

Target Market(s)

20 - 35 year old males wanting to make a change in their lives and live a legendary life.

Industry/Entity Type

Life Coaching

Font styles to use
Sans Serif
Script

Colors
ffffff
000000
33a6d7

Requirements
Must have
• Simple bold great colours. Simplicity is key
Nice to have
• I have yet to form a logo so I may need one of those built too.
Should not have
• Open to suggestions just not too busy!

```html
<!DOCTYPE html>
<html lang="en">
<head>
<meta charset="utf-8">
<title>Rise Past The Ridge Podcast</title>
<link rel="stylesheet" href="https://fonts.googleapis.com/css2?family=Stardos+Stencil:wght@700&family=Roboto:wght@400&display=swap">
<style>
  :root {
    --blue-light: #2a8fbd;
    --blue-mid: #1a6f97;
    --blue-deep: #0b4463;
    --ink: #000000;
    --paper: #ffffff;
  }
  html, body {
    margin: 0;
    padding: 0;
    width: 1200px;
    height: 1200px;
    overflow: hidden;
    background: var(--blue-mid);
  }
  .cover {
    position: relative;
    width: 1200px;
    height: 1200px;
    overflow: hidden;
  }
  .cover__backdrop {
    position: absolute;
    inset: 0;
    background: linear-gradient(180deg, var(--blue-light) 0%, var(--blue-mid) 50%, var(--blue-deep) 100%);
  }
  .cover__art {
    position: absolute;
    inset: 0;
    width: 1200px;
    height: 1200px;
  }
  .plaque {
    fill: var(--ink);
    stroke: var(--paper);
    stroke-width: 12;
    stroke-linejoin: round;
  }
  .title {
    font-family: "Stardos Stencil", "Allerta Stencil", sans-serif;
    font-weight: 700;
    font-size: 200px;
    fill: var(--paper);
  }
  .subtitle {
    font-family: "Roboto", "Helvetica Neue", sans-serif;
    font-weight: 400;
    font-size: 54px;
    fill: var(--paper);
  }
  .rule {
    stroke: var(--paper);
    stroke-width: 3;
  }
</style>
</head>
<body>
  <main class="cover">
    <div class="cover__backdrop" role="img" aria-label="Blue background with a pattern of white line-drawn social media doodles"></div>
    <svg class="cover__art" viewBox="0 0 1200 1200" xmlns="http://www.w3.org/2000/svg">
      <path class="plaque" d="
        M150,275
        C300,285 430,290 520,268
        Q600,235 680,268
        C770,290 900,285 1050,275
        A65,65 0 0 0 1125,345
        C1110,450 1120,520 1150,580
        C1120,640 1110,710 1125,815
        A65,65 0 0 0 1050,885
        C900,875 770,870 680,900
        Q600,935 520,900
        C430,870 300,875 150,885
        A65,65 0 0 0 75,815
        C90,710 80,640 50,580
        C80,520 90,450 75,345
        A65,65 0 0 0 150,275 Z"/>
      <text class="title" x="600" y="572" text-anchor="middle" textLength="912" lengthAdjust="spacingAndGlyphs">RISE PAST</text>
      <text class="title" x="600" y="772" text-anchor="middle" textLength="928" lengthAdjust="spacingAndGlyphs">THE RIDGE</text>
      <line class="rule" x1="376" y1="865" x2="448" y2="865"/>
      <text class="subtitle" x="604" y="866" text-anchor="middle" textLength="284" lengthAdjust="spacing">PODCAST</text>
      <line class="rule" x1="750" y1="865" x2="820" y2="865"/>
    </svg>
  </main>
</body>
</html>
```